Business Card Design Project

We are not a new company, but renamed to "Vantorin Kitchens" last year. We specialize in modern high-end cabinetry imports. We would like to communicate a sense of quality and cutting edge technology. Ideally the design would incorporate our logo colors, silver, red and preferably a black, matte background. Though we are open to suggestions.
Logo is attached.
Edit: I have attached rough drafts of the previous cards, this way you will have all necessary content that needs to go on the cards.
Updates
Project Deadline Extended
Reason: We have received a lot of great designs, but due to the sheer number we couldn't respond to all. We will extend the deadline for another 7 days to finalize and provide feedback to designers.
Thank you for your hard work!
Industry/Entity Type
Business
Look and feel
Each slider illustrates characteristics of the customer's brand and the style your logo design should communicate.

```html
<!DOCTYPE html>
<html lang="en">
<head>
<meta charset="utf-8">
<title>Vantorin Kitchens – Business Card</title>
<link rel="stylesheet" href="https://fonts.googleapis.com/css2?family=Arimo:wght@400;700&display=swap">
<style>
  :root {
    --backdrop: #c7d1d1;
    --card-black: #070707;
    --brand-red: #e31b23;
    --silver: #b9b9b9;
    --silver-light: #e6e6e6;
    --text-light: #f2f2f2;
    --shadow: rgba(0, 0, 0, 0.28);
  }
  * { box-sizing: border-box; margin: 0; padding: 0; }
  html, body {
    width: 1200px;
    height: 973px;
    overflow: hidden;
    background: var(--backdrop);
    font-family: "Arimo", Arial, sans-serif;
  }
  .canvas {
    position: relative;
    width: 1200px;
    height: 973px;
  }
  .card {
    position: absolute;
    width: 540px;
    height: 310px;
    background: var(--card-black);
    overflow: hidden;
    box-shadow: 0 10px 24px var(--shadow);
  }
  .card--front { left: 50px; top: 170px; }
  .card--back  { left: 610px; top: 490px; }

  .corner-art {
    position: absolute;
    inset: 0;
    width: 100%;
    height: 100%;
  }
  .identity {
    position: absolute;
    right: 22px;
    top: 14px;
    text-align: right;
    color: var(--text-light);
  }
  .identity__name {
    font-weight: 700;
    font-size: 15px;
    letter-spacing: 0.3px;
  }
  .identity__title {
    font-size: 11px;
    margin-top: 2px;
  }

  .brand {
    position: absolute;
    display: flex;
    align-items: center;
    gap: 12px;
    color: var(--silver);
    font-weight: 700;
    text-transform: uppercase;
    white-space: nowrap;
  }
  .brand__square {
    background: var(--silver);
    flex: none;
  }
  .card--front .brand {
    left: 34px;
    top: 118px;
    font-size: 30px;
    letter-spacing: 2px;
  }
  .card--front .brand__square { width: 30px; height: 30px; }

  .card--back .brand {
    left: 50%;
    top: 50%;
    transform: translate(-50%, -50%);
    font-size: 34px;
    letter-spacing: 2.5px;
  }
  .card--back .brand__square { width: 34px; height: 34px; }

  .contact {
    position: absolute;
    left: 34px;
    top: 190px;
    list-style: none;
    color: var(--text-light);
    font-size: 12.5px;
    line-height: 19px;
  }
  .contact__item {
    display: flex;
    align-items: center;
    gap: 7px;
  }
  .contact__icon {
    width: 11px;
    height: 11px;
    flex: none;
    fill: var(--brand-red);
  }
  .contact__address {
    margin-top: 8px;
  }
</style>
</head>
<body>
<main class="canvas">

  <section class="card card--front" aria-label="Business card front">
    <svg class="corner-art" viewBox="0 0 540 310" aria-hidden="true">
      <defs>
        <linearGradient id="silverBand" x1="0" y1="0" x2="1" y2="1">
          <stop offset="0" stop-color="#f4f4f4"/>
          <stop offset="0.55" stop-color="#c4c4c4"/>
          <stop offset="1" stop-color="#8d8d8d"/>
        </linearGradient>
      </defs>
      <polygon points="228,0 540,0 540,44 470,62" fill="var(--brand-red)"/>
      <polygon points="228,0 470,62 452,98" fill="url(#silverBand)"/>
      <path d="M470,62 Q520,44 540,44 L540,150 Q500,130 452,98 Z" fill="var(--card-black)"/>
      <path d="M470,62 Q500,78 452,98" fill="none" stroke="#9a9a9a" stroke-width="1"/>
    </svg>

    <div class="identity">
      <p class="identity__name">MARCUS DELANE</p>
      <p class="identity__title">Director</p>
    </div>

    <div class="brand">
      <span class="brand__square"></span>
      <span class="brand__name">Vantorin Kitchens</span>
    </div>

    <ul class="contact">
      <li class="contact__item">
        <svg class="contact__icon" viewBox="0 0 12 12" aria-hidden="true"><path d="M2.5 1 L4.5 1 L5.2 3.6 L4 4.6 Q5 7 7.4 8 L8.4 6.8 L11 7.5 L11 9.5 Q10.5 11 9 11 Q1 10 1 3 Q1 1.5 2.5 1 Z"/></svg>
        <span>780 555 0142</span>
      </li>
      <li class="contact__item">
        <svg class="contact__icon" viewBox="0 0 12 12" aria-hidden="true"><rect x="1" y="5" width="10" height="6" rx="1"/><rect x="3" y="1" width="6" height="4"/></svg>
        <span>780 555 0187</span>
      </li>
      <li class="contact__item">
        <svg class="contact__icon" viewBox="0 0 12 12" aria-hidden="true"><rect x="3" y="0.5" width="6" height="11" rx="1.2"/></svg>
        <span>780 555 0263</span>
      </li>
      <li class="contact__item">
        <svg class="contact__icon" viewBox="0 0 12 12" aria-hidden="true"><rect x="0.5" y="2.5" width="11" height="7" rx="1"/></svg>
        <span>marcus@vantorinkitchens.ca</span>
      </li>
      <li class="contact__item contact__address">
        <span>2150 - 84 Ave. Riverton, AB T5R 2K8</span>
      </li>
    </ul>
  </section>

  <section class="card card--back" aria-label="Business card back">
    <div class="brand">
      <span class="brand__square"></span>
      <span class="brand__name">Vantorin Kitchens</span>
    </div>
  </section>

</main>
</body>
</html>
```